Graphic Design Zephyrmart Book Description

There is a book on Zephyrmart that is my competitor that has a large graphic design as part of the description for the book and I want a similar thing for my book to make it stand out more.

My competitors book is here: https://www.zephyrmart.example/Stellar-Chemistry-Novices-Grasping-Walkthrough/dp/K47RTPW612/

My book is here: https://www.zephyrmart.example/Stellar-Chemistry-Groundwork-Reactions-Bonding/dp/K9HXCVT27S/

You can see the kind of thing I am looking for on the book listing but I have attached an image below.

Thanks

Trevor

```html
<!DOCTYPE html>
<html lang="en">
<head>
<meta charset="utf-8">
<title>Quantum Physics – Book Description Graphic</title>
<link rel="stylesheet" href="https://fonts.googleapis.com/css2?family=Bebas+Neue&family=Arimo:wght@400;700&family=Open+Sans:wght@400&display=swap">
<style>
:root{
  --yellow:#f2e523;
  --black:#000;
  --white:#fff;
  --ink:#0f1111;
  --link:#007185;
  --muted:#565959;
  --star:#de7921;
  --rule:#e7e7e7;
  --space-a:#3a3a40;
  --space-b:#0b0b0d;
}
*{box-sizing:border-box;margin:0;padding:0}
html,body{width:1200px;height:3322px;overflow:hidden;background:var(--white)}
body{position:relative;font-family:"Arimo",Arial,sans-serif;color:var(--ink)}
.abs{position:absolute}
.display{font-family:"Bebas Neue","Oswald",sans-serif;line-height:.86;text-transform:uppercase}
.y{color:var(--yellow)} .w{color:var(--white)}

/* carousel */
.carousel-top{top:0;left:0;width:1200px;height:14px;border-top:1px solid var(--rule)}
.carousel-title{top:26px;left:2px;font-size:14px}
.carousel-page{top:28px;right:22px;font-size:12px}
.nav-btn{top:168px;width:30px;height:30px;border:1px solid #aaa;border-radius:7px;background:#fff;display:flex;align-items:center;justify-content:center}
.item{top:64px;width:145px;font-size:11px;line-height:1.38}
.item .cover{width:84px;height:135px;margin:0 0 6px 26px}
.item .title{color:var(--link)}
.item .by{color:var(--ink);font-size:10px}
.item .by.link{color:var(--link)}
.item .stars{color:var(--star);font-size:12px;letter-spacing:-1px}
.item .stars span{color:var(--link);font-size:10px;letter-spacing:0;margin-left:4px}
.item .fmt{color:var(--muted);font-size:10px}
.item .price{font-size:13px}
.item .price sup{font-size:8px}
.item .ship{font-size:10px;color:var(--muted)}

/* hero */
.hero{top:421px;left:163px;width:870px;height:537px;background:var(--black);overflow:hidden}
.hero-title{left:64px;top:58px;font-size:74px}
.topics{left:64px;top:240px;list-style:none}
.topics li{font-family:"Bebas Neue",sans-serif;font-size:38px;color:var(--white);height:52px;display:flex;gap:16px}
.topics b{color:var(--yellow);font-weight:400}
.byline{left:64px;top:476px;font-family:"Bebas Neue",sans-serif;font-size:19px;color:var(--white)}

/* features */
.feature{top:969px;width:210px;height:209px;padding:16px 24px}
.feature.yellow{background:var(--yellow);color:var(--black)}
.feature.dark{background:var(--black);color:var(--white)}
.feature .num{position:absolute;top:14px;right:22px;font-family:"Bebas Neue",sans-serif;font-size:74px;line-height:1}
.feature .label{position:absolute;left:24px;top:100px;font-family:"Bebas Neue",sans-serif;font-size:34px;line-height:.95}
.feature-copy{top:1199px;width:190px;font-family:"Open Sans",sans-serif;font-size:12.4px;line-height:1.3;color:#222}

/* banners */
.banner{left:163px;width:870px;height:538px;overflow:hidden;background:linear-gradient(160deg,var(--space-b) 0%,var(--space-a) 42%,var(--space-b) 80%)}
.banner .shade{position:absolute;inset:0}
.big-word{font-size:290px;color:var(--white);letter-spacing:-2px}
.sub{font-size:84px;line-height:.82}
.mock{position:absolute;background:var(--yellow)}

/* details */
.details-rule{left:50px;width:1150px;border-top:1px solid var(--rule)}
.details{top:3052px;left:50px}
.details h2{font-size:24px;font-weight:400;margin-bottom:8px}
.details ul{list-style:none;margin-left:17px;font-size:13.5px;line-height:23.6px}
.details b{font-weight:700}
.details a{color:var(--link);text-decoration:none}
</style>
</head>
<body>

<!-- more items carousel -->
<div class="abs carousel-top"></div>
<div class="abs carousel-title">More items to explore</div>
<div class="abs carousel-page">Page 1 of 7</div>
<div class="abs nav-btn" style="left:6px"><svg width="10" height="14"><path d="M7 2 2 7l5 5" fill="none" stroke="#333" stroke-width="2"/></svg></div>
<div class="abs nav-btn" style="left:1146px"><svg width="10" height="14"><path d="M3 2l5 5-5 5" fill="none" stroke="#333" stroke-width="2"/></svg></div>

<div class="abs item" style="left:58px">
  <div class="cover" role="img" aria-label="Book cover: starry night sky" style="background:linear-gradient(#1c2740,#c8823a)"></div>
  <div class="title">Starlight for Busy Readers: Essays on the Cosmos and Where We Stand In It</div>
  <div class="by">Orin Calloway</div>
  <div class="stars">★★★★★<span>34,928</span></div>
  <div class="fmt">Hardcover</div>
  <div class="price"><sup>£</sup>12.99</div>
  <div class="ship">£2.74 delivery</div>
</div>
<div class="abs item" style="left:214px">
  <div class="cover" role="img" aria-label="Book cover: green nebula" style="background:linear-gradient(#14321c,#3c8a2a)"></div>
  <div class="title">Unseen Mass and Silent Force: The Missing Share of the Cos…</div>
  <div class="by link">› Dorian Vesk</div>
  <div class="stars">★★★★★<span>1,166</span></div>
  <div class="fmt">Paperback</div>
  <div class="price"><sup>£</sup>8.49</div>
  <div class="ship" style="color:var(--ink)">Get it as soon as <b>Friday, Aug 16</b></div>
  <div class="ship">£2.68 delivery</div>
</div>
<div class="abs item" style="left:371px">
  <div class="cover" role="img" aria-label="Book cover: pale sketch of equations" style="background:#ece9e2"></div>
  <div class="title">Classical Motion: The Essential Minimum</div>
  <div class="by">Milo Hartigan</div>
  <div class="stars">★★★★★<span>946</span></div>
  <div class="fmt">Paperback</div>
  <div class="price"><sup>£</sup>9.65</div>
  <div class="ship">£2.68 delivery</div>
</div>
<div class="abs item" style="left:526px">
  <div class="cover" role="img" aria-label="Book cover: dark cosmic scene" style="background:linear-gradient(#3b2516,#120c08)"></div>
  <div class="title">The Grand Theory: How the Cosmos Began and Ends</div>
  <div class="by link">› Elias Thornwood</div>
  <div class="stars">★★★★★<span>14,845</span></div>
  <div class="fmt">Paperback</div>
  <div class="price"><sup>£</sup>11.99</div>
  <div class="ship">£2.66 delivery</div>
</div>
<div class="abs item" style="left:683px">
  <div class="cover" role="img" aria-label="Book cover: glowing ring on black" style="background:radial-gradient(circle at 50% 45%,#6a3aa8,#050505 60%)"></div>
  <div class="title">Dark Stars: The Key to Reading the Cosmos</div>
  <div class="by">Professor Rowan Pike</div>
  <div class="stars">★★★★★<span>798</span></div>
  <div class="fmt">Paperback</div>
  <div class="price"><sup>£</sup>9.93</div>
  <div class="ship">£2.77 delivery</div>
</div>
<div class="abs item" style="left:838px">
  <div class="cover" role="img" aria-label="Book cover: pale sketch of equations" style="background:#ece9e2"></div>
  <div class="title">Quantum Motion: The Essential Minimum</div>
  <div class="by link">› Felix Marrow</div>
  <div class="stars">★★★★★<span>2,184</span></div>
  <div class="fmt">Paperback</div>
  <div class="price"><sup>£</sup>10.11</div>
  <div class="ship">£2.77 delivery</div>
</div>
<div class="abs item" style="left:994px">
  <div class="cover" role="img" aria-label="Book cover: black cat silhouette on white" style="background:linear-gradient(#f4f4f4,#cfcfcf)"></div>
  <div class="title">Chasing the Boxed Cat: The much-loved classic introduction to quantu…</div>
  <div class="by">Hugo Brannock</div>
  <div class="stars">★★★★★<span>1,001</span></div>
  <div class="fmt">Paperback</div>
  <div class="price"><sup>£</sup>9.85</div>
  <div class="ship">£2.77 delivery</div>
</div>

<!-- hero -->
<section class="abs hero">
  <div class="abs" role="img" aria-label="Backdrop of handwritten physics equations" style="left:410px;top:0;width:460px;height:537px;background:linear-gradient(120deg,#000 0%,#1d1d1d 55%,#0a0a0a 100%)"></div>
  <div class="mock" role="img" aria-label="Quantum Physics paperback with back cover fanned behind it" style="left:417px;top:52px;width:258px;height:418px;transform:rotate(-2deg)"></div>
  <h1 class="abs display hero-title"><span class="w">A</span> <span class="y">Beginners</span><br><span class="y">Guide</span> <span class="w">to...</span></h1>
  <ol class="abs topics">
    <li><b>01</b>Quantum Mechanics,</li>
    <li><b>02</b>String Theory,</li>
    <li><b>03</b>Field Theory, and</li>
    <li><b>04</b>Quantum Computing</li>
  </ol>
  <div class="abs byline">Written by: Silas Kendrew</div>
</section>

<!-- features -->
<div class="abs feature yellow" style="left:164px">
  <svg width="50" height="50" viewBox="0 0 50 50" fill="none" stroke="#000" stroke-width="2.5"><circle cx="25" cy="25" r="4" fill="#000"/><ellipse cx="25" cy="25" rx="22" ry="8"/><ellipse cx="25" cy="25" rx="22" ry="8" transform="rotate(60 25 25)"/><ellipse cx="25" cy="25" rx="22" ry="8" transform="rotate(-60 25 25)"/></svg>
  <div class="num">1</div><div class="label">Revolutionary<br>Concepts</div>
</div>
<div class="abs feature dark" style="left:382px">
  <svg width="50" height="50" viewBox="0 0 50 50" fill="none" stroke="#fff" stroke-width="2.5"><path d="M12 4h20l8 8v34H12z"/><path d="M18 18h16M18 25h16M18 32h16M18 39h10"/></svg>
  <div class="num">2</div><div class="label">Detailed<br>Explanations</div>
</div>
<div class="abs feature yellow" style="left:600px">
  <svg width="50" height="50" viewBox="0 0 50 50" fill="none" stroke="#000" stroke-width="2.5"><path d="M25 5a15 15 0 0 0-9 27v7h18v-7a15 15 0 0 0-9-27z"/><path d="M18 44h14M25 14v10M20 19h10"/></svg>
  <div class="num">3</div><div class="label">Thought<br>Provoking<br>Examples</div>
</div>
<div class="abs feature dark" style="left:820px">
  <svg width="50" height="50" viewBox="0 0 50 50" fill="none" stroke="#fff" stroke-width="2.5" stroke-linejoin="round"><path d="M25 4l6 14 15 1-11 10 4 15-14-8-14 8 4-15L4 19l15-1z"/></svg>
  <div class="num">4</div><div class="label">A Touch<br>of Humor</div>
</div>
<p class="abs feature-copy" style="left:177px">Lorem ipsum dolor sit amet, consectetuer adipiscing elit, sed diam nonummy nibh euismod tincidunt ut laoreet dolore magna aliquam erat volutpat. Ut wisi enim nostrud exerci tation ullamcorper suscipit lobortis nisl</p>
<p class="abs feature-copy" style="left:391px">Lorem ipsum dolor sit amet, consectetuer adipiscing elit, sed diam nonummy nibh euismod tincidunt ut laoreet dolore magna aliquam erat volutpat. Ut wisi enim nostrud exerci tation ullamcorper suscipit lobortis nisl</p>
<p class="abs feature-copy" style="left:605px">Lorem ipsum dolor sit amet, consectetuer adipiscing elit, sed diam nonummy nibh euismod tincidunt ut laoreet dolore magna aliquam erat volutpat. Ut wisi enim nostrud exerci tation ullamcorper suscipit lobortis nisl</p>
<p class="abs feature-copy" style="left:820px">Lorem ipsum dolor sit amet, consectetuer adipiscing elit, sed diam nonummy nibh euismod tincidunt ut laoreet dolore magna aliquam erat volutpat. Ut wisi enim nostrud exerci tation ullamcorper suscipit lobortis nisl</p>

<!-- embark -->
<section class="abs banner" style="top:1328px" role="region" aria-label="Embark">
  <svg class="shade" width="870" height="538" role="img" aria-label="Starry space backdrop"><polygon points="0,538 0,460 870,240 870,538" fill="#000"/></svg>
  <div class="abs display big-word" style="left:34px;top:26px">Embark</div>
  <div class="mock" role="img" aria-label="Stack of Quantum Physics paperbacks at an angle" style="left:460px;top:210px;width:330px;height:230px;transform:rotate(28deg)"></div>
  <div class="abs display sub" style="left:34px;top:322px"><span class="w">On a</span> <span class="y">Mind</span><br><span class="y">Bending Journey</span></div>
</section>

<!-- discover -->
<section class="abs banner" style="top:1875px" role="region" aria-label="Discover">
  <svg class="shade" width="870" height="538" role="img" aria-label="Galaxy backdrop"><polygon points="0,538 0,420 870,160 870,538" fill="#000"/></svg>
  <div class="abs display big-word" style="left:30px;top:24px">Discover</div>
  <div class="abs" role="img" aria-label="Open book showing chapter one pages" style="left:437px;top:206px;width:433px;height:332px;background:linear-gradient(90deg,#e9e9e9 0%,#fafafa 48%,#cfcfcf 50%,#f4f4f4 54%,#e4e4e4 100%)"></div>
  <div class="abs display sub" style="left:34px;top:286px;font-size:80px"><span class="w">The Secrets</span><br><span class="w">of</span> <span class="y">the Quantum</span><br><span class="y">Universe</span></div>
</section>

<!-- unlock -->
<section class="abs banner" style="top:2422px;left:159px;width:875px;height:542px" role="region" aria-label="Unlock">
  <svg class="shade" width="875" height="542" role="img" aria-label="Starry space backdrop"><polygon points="0,542 0,470 875,250 875,542" fill="#000"/></svg>
  <div class="abs display big-word" style="left:36px;top:40px">Unlock</div>
  <svg class="abs" style="left:748px;top:58px" width="70" height="70" viewBox="0 0 50 50" fill="none" stroke="#fff" stroke-width="2.5"><circle cx="25" cy="25" r="4" fill="#fff"/><ellipse cx="25" cy="25" rx="22" ry="8"/><ellipse cx="25" cy="25" rx="22" ry="8" transform="rotate(60 25 25)"/><ellipse cx="25" cy="25" rx="22" ry="8" transform="rotate(-60 25 25)"/></svg>
  <div class="mock" role="img" aria-label="Quantum Physics back cover" style="left:404px;top:176px;width:210px;height:318px"></div>
  <div class="mock" role="img" aria-label="Quantum Physics front cover" style="left:628px;top:176px;width:210px;height:318px"></div>
  <div class="abs display sub" style="left:53px;top:343px;font-size:62px"><span class="w">The Power</span><br><span class="y">of Quantum</span><br><span class="y">Mechanics</span></div>
</section>

<!-- product details -->
<div class="abs details-rule" style="top:3032px"></div>
<section class="abs details">
  <h2>Product details</h2>
  <ul>
    <li><b>ASIN&nbsp;:</b> K9HXCVT27S</li>
    <li><b>Publisher&nbsp;:</b> Independently published (8 Jun. 2024)</li>
    <li><b>Language&nbsp;:</b> English</li>
    <li><b>Paperback&nbsp;:</b> 175 pages</li>
    <li><b>ISBN-13&nbsp;:</b> 979-8000412275</li>
    <li><b>Dimensions&nbsp;:</b> 15.24 x 1.02 x 22.86 cm</li>
    <li><b>Best Sellers Rank:</b> 188,945 in Books (<a>See Top 100 in Books</a>)</li>
    <li><b>Customer reviews:</b> 4.9 <span style="color:var(--star)">★★★★★</span> ⌄ &nbsp; <a>29 ratings</a></li>
  </ul>
</section>
<div class="abs details-rule" style="top:3276px"></div>

</body>
</html>
```